Marwick Law Letterhead

We need a new letterhead design for a Law Firm. The address for the law firm is 1475 Calloway Street, Suite 210, Houston, Texas 77041. Phone Number: 832-361-9027; Fax Number: 832-614-7359. The logo is uploaded to the project.

```html
<!DOCTYPE html>
<html lang="en">
<head>
<meta charset="utf-8">
<title>Marwick Law Letterhead</title>
<link rel="stylesheet" href="https://fonts.googleapis.com/css2?family=Montserrat:wght@300;400;500;600;700&display=swap">
<style>
  :root {
    --navy: #1b2f5e;
    --red: #c8161e;
    --red-dark: #8f0a12;
    --ink: #222222;
    --paper: #ffffff;
    --backdrop: #cfcfcf;
  }
  * { margin: 0; padding: 0; box-sizing: border-box; }
  html, body {
    width: 1200px; height: 1200px; overflow: hidden;
    background: var(--backdrop);
    font-family: "Montserrat", sans-serif;
  }
  .letterhead {
    position: absolute; left: 136px; top: 0;
    width: 928px; height: 1200px;
    background: var(--paper);
    overflow: hidden;
    color: var(--ink);
  }
  .firm-name {
    position: absolute; left: 68px; top: 66px;
    font-size: 36px; font-weight: 600; color: var(--navy);
    letter-spacing: 0.5px; line-height: 1;
  }
  .contact-frame {
    position: absolute; left: 429px; top: 29px;
    width: 520px; height: 119px;
    border: 4px solid var(--navy); border-right: none;
    border-radius: 40px 0 0 40px;
    background: var(--paper);
  }
  .contact-bar {
    position: absolute; left: 441px; top: 39px;
    width: 500px; height: 99px;
    border-radius: 30px 0 0 30px;
    background: linear-gradient(180deg, var(--red-dark) 0%, var(--red) 100%);
    color: #fff;
  }
  .phone-line {
    position: absolute; left: 33px;
    display: flex; align-items: center; gap: 10px;
    font-size: 22px; font-weight: 600; letter-spacing: 1px;
  }
  .phone-line svg { width: 17px; height: 17px; }
  .phone-line.voice { top: 18px; }
  .phone-line.fax { top: 50px; }
  .bar-divider {
    position: absolute; left: 246px; top: 27px;
    width: 2px; height: 46px; background: #fff;
  }
  .address {
    position: absolute; left: 264px; top: 22px;
    font-size: 14.5px; font-weight: 600; line-height: 18px; letter-spacing: 0.6px;
  }
  .subject {
    position: absolute; left: 73px; top: 237px;
    font-size: 20px; font-weight: 700; letter-spacing: 0.3px;
  }
  .subject-note {
    position: absolute; left: 73px; top: 270px;
    font-size: 15px; font-weight: 400;
  }
  .body-copy { position: absolute; left: 74px; top: 322px; width: 760px; }
  .body-copy p {
    font-size: 18.3px; font-weight: 400; line-height: 25.8px; letter-spacing: 0.15px;
    margin-bottom: 23.5px; white-space: nowrap;
  }
  .sign-off {
    position: absolute; right: 102px; top: 1021px;
    text-align: right; font-size: 20px; font-weight: 700; line-height: 26px;
  }
  .footer-band {
    position: absolute; left: 0; bottom: 0;
    width: 100%; height: 47px;
    background: linear-gradient(180deg, var(--red-dark) 0%, var(--red) 100%);
  }
  .footer-fold {
    position: absolute; left: 400px; top: 1143px;
    width: 26px; height: 14px; border-radius: 6px 6px 0 0;
    background: #0f1d3d;
  }
  .web-tab {
    position: absolute; left: 0; top: 1143px;
    width: 409px; height: 44px;
    background: var(--navy);
    border-radius: 0 0 10px 0;
    color: #fff;
    font-size: 24px; font-weight: 500; letter-spacing: 1.6px;
    line-height: 44px; padding-left: 58px;
  }
</style>
</head>
<body>
<main class="letterhead">
  <div class="firm-name">Marwick Law</div>

  <div class="contact-frame"></div>
  <div class="contact-bar">
    <div class="phone-line voice">
      <svg viewBox="0 0 24 24" aria-hidden="true"><path fill="#fff" d="M6.6 10.8a15.1 15.1 0 0 0 6.6 6.6l2.2-2.2c.3-.3.7-.4 1-.2 1.1.4 2.3.6 3.6.6.6 0 1 .4 1 1V20c0 .6-.4 1-1 1A17 17 0 0 1 3 4c0-.6.4-1 1-1h3.5c.6 0 1 .4 1 1 0 1.3.2 2.5.6 3.6.1.3 0 .7-.2 1z"/></svg>
      <span>832-361-9027</span>
    </div>
    <div class="phone-line fax">
      <svg viewBox="0 0 24 24" aria-hidden="true"><path fill="#fff" d="M7 2h8l3 3v5h2a2 2 0 0 1 2 2v9a1 1 0 0 1-1 1H3a1 1 0 0 1-1-1v-9a2 2 0 0 1 2-2h3zm2 2v6h7V6h-2V4zm1 9v2h2v-2zm4 0v2h2v-2zm-4 4v2h2v-2zm4 0v2h2v-2zM4 12v8h3v-8z"/></svg>
      <span>832-614-7359</span>
    </div>
    <div class="bar-divider"></div>
    <div class="address">1475 Calloway Street,<br>Suite 210, Houston,<br>Texas 77041</div>
  </div>

  <h1 class="subject">Lorem Ipsum is simply</h1>
  <div class="subject-note">Lorem Ipsum is simply</div>

  <section class="body-copy">
    <p>Lorem Ipsum is simply dummy text of the printing and typesetting industry.<br>Lorem Ipsum has been the industry's standard dummy text ever since the<br>1500s, when an unknown printer took a galley of type and scrambled it to make<br>a type specimen book. It has survived not only five centuries, but also the leap<br>into electronic typesetting, remaining essentially unchanged. It was popularised<br>in the 1960s with the release of Typemoor sheets containing Lorem Ipsum<br>passages, and more recently with desktop publishing software like Orwin<br>PageForge including versions of Lorem Ipsum.</p>
    <p>Lorem Ipsum is simply dummy text of the printing and typesetting industry.<br>Lorem Ipsum has been the industry's standard dummy text ever since the<br>1500s, when an unknown printer took a galley of type and scrambled it to make<br>a type specimen book. It has survived not only five centuries, but also the leap<br>into electronic typesetting, remaining essentially unchanged. It was popularised<br>in the 1960s with the release of Typemoor sheets containing Lorem Ipsum<br>passages, and more recently with desktop publishing software like Orwin<br>PageForge including versions of Lorem Ipsum.</p>
    <p>Lorem Ipsum is simply dummy text of the printing and typesetting industry.<br>Lorem Ipsum has been the industry's standard dummy text ever since the<br>1500s, when an unknown printer took a galley of type and scrambled it to make<br>a type specimen book. It has survived not only five centuries, but also the leap<br>into electronic typesetting, remaining essentially unchanged. It was popularised<br>in the 1960s with the release of Typemoor sheets containing Lorem Ipsum<br>passages, and more recently with desktop publishing software like Orwin<br>PageForge including versions of Lorem Ipsum.</p>
  </section>

  <div class="sign-off">Lorem Ipsum<br>is simply</div>

  <div class="footer-band"></div>
  <div class="footer-fold"></div>
  <div class="web-tab">www.marwick@law.com</div>
</main>
</body>
</html>
```